Gobal construction supply company needs new business card design

I need a business card design for my global supply company using an existing logo. i will be looking to print these on rounded corner cards with the black background version of my logo on the back. on the front white background, my logo again and my simple details.

```html
<!DOCTYPE html>
<html lang="en">
<head>
<meta charset="utf-8">
<title>Meridian Build Supply – Business Card</title>
<link rel="stylesheet" href="https://fonts.googleapis.com/css2?family=Roboto:wght@400;500;700&display=swap">
<style>
  :root{
    --stage:#8c8c8c;
    --card-white:#f4f4f4;
    --card-black:#1b1b1b;
    --ink:#111111;
    --text-grey:#555555;
    --accent-red:#d60000;
    --white:#ffffff;
  }
  *{margin:0;padding:0;box-sizing:border-box}
  html,body{width:1200px;height:960px;overflow:hidden}
  body{background:var(--stage);font-family:"Roboto",Arial,sans-serif;position:relative}

  .card{position:absolute;width:600px;height:343px;border-radius:18px;overflow:hidden}

  /* front */
  .card-front{left:82px;top:103px;background:var(--card-white)}
  .card-front .base-band{position:absolute;left:0;right:0;bottom:0;height:17px;background:var(--ink)}
  .card-front .name-tab{position:absolute;right:0;top:35px;width:18px;height:38px;background:var(--accent-red)}

  .brand{position:absolute;display:flex;align-items:center;gap:10px}
  .brand-mark{width:20px;height:20px;background:var(--accent-red);flex:none}
  .brand-name{font-weight:700;font-size:21px;letter-spacing:.2px;white-space:nowrap}
  .card-front .brand{left:44px;top:125px}
  .card-front .brand-name{color:var(--ink)}

  .identity{position:absolute;right:44px;top:34px;text-align:right}
  .identity-name{font-weight:500;font-size:22px;color:var(--ink);line-height:26px}
  .identity-role{font-weight:500;font-size:14.5px;color:var(--accent-red);line-height:17px}

  .contacts{position:absolute;left:44px;top:201px;list-style:none}
  .contacts li{display:flex;align-items:center;height:19px;font-size:14.5px;color:var(--text-grey)}
  .contacts svg{width:14px;height:14px;margin-right:8px;fill:var(--ink);flex:none}

  .address{position:absolute;left:383px;top:257px;font-size:14.5px;line-height:18px;color:var(--text-grey);font-style:normal}

  /* back */
  .card-back{left:439px;top:488px;background:var(--card-black)}
  .card-back .brand{left:50%;top:50%;transform:translate(-50%,-50%)}
  .card-back .brand-name{color:var(--white);font-size:23px}
</style>
</head>
<body>

<section class="card card-front" aria-label="Card front">
  <div class="brand">
    <span class="brand-mark"></span>
    <span class="brand-name">MERIDIAN BUILD SUPPLY</span>
  </div>

  <div class="identity">
    <p class="identity-name">DANIEL HART</p>
    <p class="identity-role">CEO/FOUNDER</p>
  </div>
  <span class="name-tab"></span>

  <ul class="contacts">
    <li><svg viewBox="0 0 24 24"><path d="M6.6 10.8a15.1 15.1 0 0 0 6.6 6.6l2.2-2.2c.3-.3.7-.4 1-.2 1.1.4 2.3.6 3.6.6.6 0 1 .4 1 1V20c0 .6-.4 1-1 1A17 17 0 0 1 3 4c0-.6.4-1 1-1h3.5c.6 0 1 .4 1 1 0 1.3.2 2.5.6 3.6.1.3 0 .7-.2 1z"/></svg>612 555 0148</li>
    <li><svg viewBox="0 0 24 24"><path d="M7 1h10a2 2 0 0 1 2 2v18a2 2 0 0 1-2 2H7a2 2 0 0 1-2-2V3a2 2 0 0 1 2-2zm0 3v14h10V4z"/></svg>612 555 0193</li>
    <li><svg viewBox="0 0 24 24"><path d="M6 2h12v5H6zM3 8h18a2 2 0 0 1 2 2v7h-4v5H5v-5H1v-7a2 2 0 0 1 2-2zm4 7v5h10v-5z"/></svg>612 555 0176</li>
    <li><svg viewBox="0 0 24 24"><path d="M2 5h20v14H2zm2 2v.5l8 5 8-5V7z"/></svg>daniel@meridianbuild.com</li>
    <li><svg viewBox="0 0 24 24"><path d="M12 2a10 10 0 1 0 0 20 10 10 0 0 0 0-20zm-1 17.9A8 8 0 0 1 4.2 10L9 14.8V16a2 2 0 0 0 2 2zm6.9-2.5A2 2 0 0 0 16 16h-1v-3a1 1 0 0 0-1-1H8v-2h2a1 1 0 0 0 1-1V7h2a2 2 0 0 0 2-2v-.4a8 8 0 0 1 2.9 12.8z"/></svg>www.meridianbuild.com</li>
  </ul>

  <address class="address">48 Foundry Street<br>Geelong, Victoria 3220</address>

  <span class="base-band"></span>
</section>

<section class="card card-back" aria-label="Card back">
  <div class="brand">
    <span class="brand-mark"></span>
    <span class="brand-name">MERIDIAN BUILD SUPPLY</span>
  </div>
</section>

</body>
</html>
```